m-brightscan needs new website

need to get completely new updated site for m-brightscan.example
general business concepts can be started from that site and I can offer specifick input about business operations and goals. would like to offer on-line ordering, service requests, and payments if possible.

```html
<!DOCTYPE html>
<html lang="en">
<head>
<meta charset="utf-8">
<title>M-Brightscan International</title>
<link href="https://fonts.googleapis.com/css2?family=Lato:wght@400;700&display=swap" rel="stylesheet">
<style>
:root{
  --red:#e8202a;
  --ink:#222222;
  --text:#333333;
  --muted:#666666;
  --rule:#e4e4e4;
  --nav-bg:#f7f7f7;
  --section-bg:#f5f5f5;
  --footer-bg:#000000;
  --field-bg:#1e1e1e;
  --white:#ffffff;
}
*{margin:0;padding:0;box-sizing:border-box}
html,body{width:677px;height:1200px;overflow:hidden}
body{position:relative;background:var(--white);font-family:'Lato',sans-serif;color:var(--text)}
.abs{position:absolute}

/* header */
.brand{left:45px;top:20px;display:flex;align-items:center;gap:6px}
.brand-mark{width:14px;height:14px;border-radius:50%;background:var(--red)}
.brand-name{font-size:14px;font-weight:700;color:var(--ink);line-height:1.05}
.top-contact{top:25px;font-size:8.5px;display:flex;align-items:center;gap:6px}
.top-email{left:424px;color:var(--red)}
.top-phone{left:564px;color:var(--ink)}

/* nav */
.nav{left:0;top:62px;width:677px;height:28px;background:var(--nav-bg);border-top:1px solid var(--rule);border-bottom:1px solid var(--rule)}
.nav-item{top:0;height:27px;line-height:27px;text-align:center;font-size:8.5px;color:var(--ink);border-right:1px solid var(--rule);letter-spacing:.3px}
.nav-item.active{background:var(--red);color:var(--white)}
.search{left:502px;top:6px;width:130px;height:15px;background:#e9e9e9;font-size:8px;color:#aaa;padding-left:8px;line-height:15px}
.search-btn{right:2px;top:2px;width:11px;height:11px;background:var(--white);border:1px solid #ddd}
.dropdown{left:268px;top:90px;width:72px;z-index:5;background:#f2f2f2}
.dropdown div{height:21.5px;line-height:21.5px;padding-left:18px;font-size:8px;color:var(--ink);border-bottom:1px solid var(--rule)}

/* hero */
.hero{left:0;top:90px;width:677px;height:323px;background:linear-gradient(120deg,#3a4050 0%,#d9dde2 40%,#eef0f2 60%,#8b8f99 100%)}
.hero-product{left:120px;top:264px;width:232px;height:176px;background:linear-gradient(160deg,#2b2d31,#111215);border-radius:6px}
.hero-caption{left:46px;top:280px;width:198px;height:66px;background:rgba(30,30,30,.72);color:var(--white);padding:12px 0 0 21px;z-index:2}
.hero-caption h2{font-size:20px;font-weight:400;line-height:1}
.hero-caption p{font-size:7.5px;line-height:1.3;margin-top:2px}
.dots{left:46px;top:349px;width:28px;height:9px;background:rgba(0,0,0,.6);display:flex;gap:3px;padding:3px 0 0 8px}
.dots span{width:3px;height:3px;background:var(--white)}
.dots span:first-child{background:var(--red)}
.arrow{top:382px;width:20px;height:17px;background:var(--red);display:flex;align-items:center;justify-content:center}

/* sections */
.section-title{font-size:16px;font-weight:400;color:var(--ink)}
.title-rule{width:46px;height:2px;background:var(--red)}
.body-copy{font-size:7.8px;line-height:13.6px;color:var(--text)}
.btn{width:102px;height:23px;background:var(--red);color:var(--white);font-size:8px;text-align:center;line-height:23px}
.about-photo{left:419px;top:470px;width:212px;height:212px;border-radius:50%;background:radial-gradient(circle at 45% 45%,#f2e6e0,#c9a596 60%,#8f7366)}
.solutions{left:0;top:728px;width:677px;height:268px;background:var(--section-bg)}
.sol-frame{left:342px;top:768px;width:292px;height:206px;background:#e3e7eb}
.sol-photo{left:355px;top:780px;width:267px;height:182px;background:linear-gradient(135deg,#1e5a86,#4b9fcf 55%,#1a4d72);border:1px solid #14405f}

/* footer */
.footer{left:0;top:996px;width:677px;height:172px;background:var(--footer-bg);color:var(--white)}
.f-brand{left:43px;top:1036px;display:flex;align-items:center;gap:6px}
.f-brand .brand-name{color:var(--white)}
.f-about{left:46px;top:1074px;width:120px;font-size:7.2px;font-weight:700;line-height:9.5px;color:var(--white)}
.f-more{left:44px;top:1124px;font-size:7.5px;font-weight:700;color:var(--white);display:flex;align-items:center;gap:4px}
.f-head{font-size:8px;font-weight:700;color:var(--white)}
.f-rule{width:26px;height:2px;background:var(--white);margin-top:4px}
.f-links{left:202px;top:1065px;list-style:none;font-size:7.5px;color:var(--white)}
.f-links li{height:14px;line-height:14px}
.f-links li::before{content:"";display:inline-block;width:2px;height:2px;background:var(--white);margin-right:8px;vertical-align:middle}
.f-contact{left:300px;top:1064px;font-size:7.5px;font-weight:700;color:var(--white)}
.f-contact div{height:14.4px;line-height:14.4px;display:flex}
.f-contact b{display:inline-block;width:42px;font-weight:700}
.field{background:var(--field-bg);font-size:7px;color:#bbb;padding:4px 0 0 7px;border:1px solid #2a2a2a;letter-spacing:.4px}
.send{left:557px;top:1117px;width:74px;height:13px;background:var(--red);color:var(--white);font-size:7px;font-weight:700;text-align:center;line-height:13px;letter-spacing:.6px}
.copyright{left:46px;top:1177px;font-size:7.5px;color:var(--ink)}
.social{top:1177px;width:10px;height:10px;border-radius:50%;background:#333}
</style>
</head>
<body>

<header>
  <div class="abs brand"><span class="brand-mark"></span><span class="brand-name">M-BRIGHTSCAN<br>International</span></div>
  <div class="abs top-contact top-email">
    <svg width="11" height="8" viewBox="0 0 11 8"><rect x=".5" y=".5" width="10" height="7" fill="#333"/><path d="M.5 .5 5.5 4.5 10.5 .5" stroke="#fff" fill="none" stroke-width=".8"/></svg>
    support@m-brightscan.example
  </div>
  <div class="abs top-contact top-phone">
    <svg width="9" height="9" viewBox="0 0 24 24"><path fill="#333" d="M6.6 10.8a15 15 0 0 0 6.6 6.6l2.2-2.2c.3-.3.7-.4 1-.2 1.1.4 2.3.6 3.6.6.6 0 1 .4 1 1V20c0 .6-.4 1-1 1A17 17 0 0 1 3 4c0-.6.4-1 1-1h3.5c.6 0 1 .4 1 1 0 1.3.2 2.5.6 3.6.1.3 0 .7-.2 1z"/></svg>
    555-014-8125
  </div>
</header>

<nav class="abs nav">
  <div class="abs nav-item active" style="left:45px;width:72px">Home</div>
  <div class="abs nav-item" style="left:117px;width:69px">About us</div>
  <div class="abs nav-item" style="left:186px;width:82px">Our Mission</div>
  <div class="abs nav-item" style="left:268px;width:72px">Solutions &#9666;</div>
  <div class="abs nav-item" style="left:340px;width:72px">Partners</div>
  <div class="abs nav-item" style="left:412px;width:79px">Contact us</div>
  <div class="abs search">Search..
    <div class="abs search-btn"><svg width="9" height="9" viewBox="0 0 10 10"><circle cx="4.3" cy="4.3" r="2.3" stroke="#e8202a" fill="none" stroke-width="1.1"/><path d="M6 6l2 2" stroke="#e8202a" stroke-width="1.1"/></svg></div>
  </div>
</nav>
<div class="abs dropdown"><div>Hardware</div><div>Software</div></div>

<section>
  <div class="abs hero" role="img" aria-label="Photo of two business people shaking hands over a desk with documents"></div>
  <div class="abs hero-product" role="img" aria-label="Photo of a desktop check scanner"></div>
  <div class="abs hero-caption">
    <h2>Branch Capture</h2>
    <p>Scan and Transmit check images directly<br>from branch to processing site</p>
  </div>
  <div class="abs dots"><span></span><span></span><span></span></div>
  <div class="abs arrow" style="left:588px"><svg width="8" height="10" viewBox="0 0 8 10"><path d="M6 1 2 5l4 4" stroke="#fff" stroke-width="1.8" fill="none"/></svg></div>
  <div class="abs arrow" style="left:611px"><svg width="8" height="10" viewBox="0 0 8 10"><path d="M2 1l4 4-4 4" stroke="#fff" stroke-width="1.8" fill="none"/></svg></div>
</section>

<section>
  <h2 class="abs section-title" style="left:45px;top:494px">About us</h2>
  <div class="abs title-rule" style="left:45px;top:526px"></div>
  <div class="abs body-copy" style="left:45px;top:540px;width:340px">
    <p>M-Brightscan is an Imaging Solutions company based out of Central Illinois. Being from a small town, we keep our roots in honesty and hospitality, yet our product solutions are on the cutting edge of technology.</p>
    <p style="margin-top:13.6px">We not only provide our customers valuable solutions, we do it well. We underst and the needs of the institutions we serve and have the means to stay up to date on the latest advancements in the industry. From simple check archive to complex corporate</p>
  </div>
  <div class="abs btn" style="left:45px;top:662px">Read More</div>
  <div class="abs about-photo" role="img" aria-label="Photo of a hand signing a check with a gold pen"></div>
</section>

<section>
  <div class="abs solutions"></div>
  <h2 class="abs section-title" style="left:46px;top:780px">Solutions For Your Business</h2>
  <div class="abs title-rule" style="left:46px;top:810px;width:72px"></div>
  <p class="abs body-copy" style="left:46px;top:826px;width:282px;text-align:justify;letter-spacing:.2px">M-BRIGHTSCAN strives to be the leading provider of cost-effective solutions to the Retail, Wholesale and Banking Marketplace. Our experience in supplying complete software, hardware, and turnkey systems enables us to provide a system that fits your needs, we don't believe in trying to change your operations to fit our products.</p>
  <div class="abs btn" style="left:45px;top:907px">Read More</div>
  <div class="abs sol-frame"></div>
  <div class="abs sol-photo" role="img" aria-label="Photo of a check scanner on a blue background"></div>
</section>

<footer>
  <div class="abs footer"></div>
  <div class="abs f-brand"><span class="brand-mark"></span><span class="brand-name">M-BRIGHTSCAN<br>International</span></div>
  <p class="abs f-about">Lorem Ipsum is simply dummy text of the printing and types etting industry. Lorem Ipsum</p>
  <div class="abs f-more">Read More..
    <svg width="8" height="8" viewBox="0 0 8 8"><circle cx="4" cy="4" r="3.3" stroke="#fff" fill="none" stroke-width=".8"/><path d="M3.3 2.5 4.8 4 3.3 5.5" stroke="#fff" fill="none" stroke-width=".8"/></svg>
  </div>

  <div class="abs" style="left:202px;top:1036px"><div class="f-head">Quick Link</div><div class="f-rule"></div></div>
  <ul class="abs f-links">
    <li>Home</li><li>About us</li><li>Our Mission</li><li>Applications</li><li>Contact us</li>
  </ul>

  <div class="abs" style="left:300px;top:1036px"><div class="f-head">Contact us</div><div class="f-rule" style="width:38px"></div></div>
  <div class="abs f-contact">
    <div><b>Address :</b>42 Harbor Lane</div>
    <div><b></b>Millbrook, IL 60000</div>
    <div><b>Phone&nbsp;&nbsp;&nbsp;:</b>+555-014-7959</div>
    <div><b>Fax&nbsp;&nbsp;&nbsp;&nbsp;&nbsp;&nbsp;&nbsp;:</b>555-014-8125</div>
    <div><b>E-mail&nbsp;&nbsp;:</b>support@m-brightscan.example</div>
  </div>

  <div class="abs" style="left:477px;top:1036px"><div class="f-head">Quick Contact</div><div class="f-rule" style="width:38px"></div></div>
  <div class="abs field" style="left:477px;top:1065px;width:74px;height:15px">Name</div>
  <div class="abs field" style="left:557px;top:1065px;width:74px;height:15px">Phone</div>
  <div class="abs field" style="left:477px;top:1087px;width:154px;height:23px">Message</div>
  <div class="abs send">SEND</div>

  <p class="abs copyright">Copyright 2019 m-brightscan International, All Rights Reserved.</p>
  <span class="abs social" style="left:534px"></span>
  <span class="abs social" style="left:555px"></span>
  <span class="abs social" style="left:577px"></span>
  <span class="abs social" style="left:598px"></span>
  <span class="abs social" style="left:620px"></span>
</footer>

</body>
</html>
```